A new updated business card. A good first impression for new customers to our business.

I need something unique. I will attached a picture of our old rubbish cards, and also our current Logo ( I think this needs an update if you have any ideas, its very basic and budget)The best way you will get to see my business is checking our Facebook page, I don't really know what else to say, but anything you want to know, ask away.www.facebook.com/tkwashandseal/

Target Market(s)

Home owners

Industry/Entity Type

Business

Contact Information for Business Card

T&K's Pressure Cleaning & Concrete Sealing
Maya 0492 615 370 maya@tkwashandseal.com
Dylan 0431 528 906 dylan@tkwashandseal.com

FB: www.facebook.com/tkwashandseal/
Website: www.tkwashandseal.net (This is pretty rubbish- we don't really use it)

100% customer satisfaction guaranteed

All aspects of Hi-Pressure Cleaning
Sealing & Re-Sealing
Roof Cleaning
Colour sealing
Decorative coatings

Free no obligation quotes

Requirements
Must have
• NO OBLIGATION FREE quotes
• 100% Customer satisfaction guaranteed
• Can you please add both names, contact details and email address on one card.
• Dylan 0431 528 906
• dylan@tkwashandseal.com
• Maya 0492 615 370
• maya@tkwashandseal.com
• Please change the services:
• Hot/Cold Hi-Pressure Cleaning
• Sealing & Re-Sealing
• Roof Cleaning
• Colour Sealing
• Decorative Coatings
• Concrete Honing
• Thanks
Nice to have
• Something a bit different, something eye catching.l

```html
<!DOCTYPE html>
<html lang="en">
<head>
<meta charset="utf-8">
<title>T&amp;K's Pressure Cleaning – Business Card</title>
<link rel="stylesheet" href="https://fonts.googleapis.com/css2?family=Open+Sans:ital,wght@0,400;0,600;0,700;1,700&display=swap">
<style>
  :root {
    --page-bg: #9b9b9b;
    --card-white: #f1f1f1;
    --brand-red: #d50000;
    --ink: #3a3a3a;
    --ink-soft: #555555;
    --rule-grey: #6f6f6f;
    --on-red: #ffffff;
    --badge-gold: #c9962e;
    --badge-ring: #f4d27a;
    --badge-ribbon: #a30f0f;
  }
  * { box-sizing: border-box; margin: 0; padding: 0; }
  html, body {
    width: 1105px; height: 1200px; overflow: hidden;
    background: var(--page-bg);
    font-family: "Open Sans", Arial, sans-serif;
  }
  .card { position: absolute; left: 182px; width: 746px; }

  /* Front */
  .card-front { top: 119px; height: 427px; background: var(--card-white); }
  .brand-mark {
    position: absolute; left: 44px; top: 70px;
    display: flex; align-items: center; gap: 16px;
  }
  .brand-dot { width: 22px; height: 22px; border-radius: 50%; background: var(--brand-red); flex: none; }
  .brand-name { font-size: 24px; font-weight: 700; color: var(--ink); line-height: 1.25; width: 340px; }
  .contact { position: absolute; top: 260px; }
  .contact-dylan { left: 43px; }
  .contact-maya { left: 400px; }
  .contact-name { font-size: 28px; font-weight: 600; color: var(--brand-red); line-height: 36px; }
  .contact-phone { font-size: 23px; font-weight: 600; color: var(--ink); line-height: 36px; margin-top: 2px; }
  .contact-line { font-size: 19.5px; color: var(--ink-soft); line-height: 30px; }
  .column-divider { position: absolute; left: 377px; top: 268px; width: 2px; height: 117px; background: var(--ink); }
  .edge-rule { position: absolute; left: 0; right: 0; top: 408px; height: 3px; background: var(--rule-grey); }
  .edge-band { position: absolute; left: 0; right: 0; bottom: 0; height: 14px; background: var(--brand-red); }

  /* Back */
  .card-back {
    top: 637px; height: 425px;
    background: var(--brand-red); color: var(--on-red); text-align: center;
  }
  .guarantee {
    position: absolute; right: 24px; top: 14px;
    display: flex; align-items: center; gap: 10px;
  }
  .guarantee-text {
    font-size: 13px; font-weight: 700; line-height: 17px;
    text-align: right; text-transform: uppercase; letter-spacing: 0.3px;
  }
  .back-brand {
    position: absolute; left: 0; right: 0; top: 150px;
    font-size: 34px; font-weight: 700; line-height: 1.2;
  }
  .services {
    position: absolute; left: 0; right: 0; top: 296px;
    font-size: 19px; line-height: 29px;
  }
  .services .sep { margin: 0 6px; font-size: 12px; vertical-align: 2px; }
  .quote-offer {
    position: absolute; left: 0; right: 0; top: 360px;
    font-size: 21px; font-weight: 700; font-style: italic; line-height: 30px;
  }
</style>
</head>
<body>
  <section class="card card-front" aria-label="Business card front">
    <div class="brand-mark">
      <span class="brand-dot"></span>
      <span class="brand-name">T&amp;K's Pressure Cleaning &amp; Concrete Sealing</span>
    </div>

    <div class="contact contact-dylan">
      <p class="contact-name">Dylan</p>
      <p class="contact-phone">0431 528 906</p>
      <p class="contact-line">dylan@tkwashandseal.com</p>
      <p class="contact-line">facebook.com/tkwashandseal</p>
    </div>
    <div class="column-divider"></div>
    <div class="contact contact-maya">
      <p class="contact-name">Maya</p>
      <p class="contact-phone">0492 615 370</p>
      <p class="contact-line">maya@tkwashandseal.com</p>
      <p class="contact-line">www.tkwashandseal.net</p>
    </div>

    <div class="edge-rule"></div>
    <div class="edge-band"></div>
  </section>

  <section class="card card-back" aria-label="Business card back">
    <div class="guarantee">
      <p class="guarantee-text">100% Customer<br>Satisfaction<br>Guaranteed</p>
      <svg width="64" height="80" viewBox="0 0 72 86" role="img" aria-label="Satisfaction guarantee seal">
        <polygon points="20,50 12,84 24,76 32,84 36,56" fill="var(--badge-ribbon)"/>
        <polygon points="52,50 60,84 48,76 40,84 36,56" fill="var(--badge-ribbon)"/>
        <circle cx="36" cy="34" r="32" fill="var(--badge-gold)"/>
        <circle cx="36" cy="34" r="24" fill="none" stroke="var(--badge-ring)" stroke-width="3"/>
      </svg>
    </div>

    <p class="back-brand">T&amp;K's Pressure Cleaning</p>

    <div class="services">
      <p>Hot/Cold Hi-Pressure Cleaning<span class="sep">●</span>Sealing &amp; Re-Sealing<span class="sep">●</span>Roof Cleaning</p>
      <p>Colour Sealing<span class="sep">●</span>Decorative Coatings<span class="sep">●</span>Concrete Honing</p>
    </div>
    <p class="quote-offer">Free no obligation quotes</p>
  </section>
</body>
</html>
```